CalmPeak Nurses' Manifesto

Design a manifesto to inspire and motivate nurses to work at minimum standards of excellence in their nursing practice.

The manifesto will become a feature of our website, at conferences, workshops and retreats. It will also be featured on other marketing tools.

Primary Market:
Nurses and/or other healthcare professionals (specifically Doctors, Occupational Therapists, Psychologists and Social Workers).

However the manifesto is equally applicable to all nurses and healthcare professionals from new graduates to very experienced senior clinicians, administration officers,managers and healthcare executive personnel.

Mainly females and primarily 35 to 65 years old, which suggests people in this target age group have extensive experience, but have become jaded'.

The purpose of our business is to assist healthcare professionals, primarily nurses, to maintain their enthusiasm and excellence in service provision, for their benefit as well as the benefit of the clients.

I have attached:
File 1: Copy Samples and examples: which has the copy for the manifesto, examples that appeal to us and our 3 attempts.
File 2: Our colour Spec Sheet, HOWEVER the colours are not necessary limited to these colours. These colours are not in the logo that will be on the manifesto. The colours on the logo attached can/or also be used.
File 3: Prototype logo. The final logo will be available within 3 to 4 days.

Industry/Entity Type

Healthcare

Requirements
Must have
• Must use the copy as per the attached file.

It should be contemporary, eye catching and motivational.

Should not have
• MUST BE EASY TO READ. Each line MUST be clearly defined from each other.

```html
<!DOCTYPE html>
<html lang="en">
<head>
<meta charset="utf-8">
<title>CalmPeak Nurses' Manifesto</title>
<link rel="stylesheet" href="https://fonts.googleapis.com/css2?family=Oswald:wght@500;700&family=Anton&display=swap">
<style>
:root{
  --cream:#fbf3df;
  --frame:#f08a24;
  --navy:#1e2b3c;
  --teal:#25a5b5;
  --orange:#ee8a22;
  --white:#ffffff;
}
*{margin:0;padding:0;box-sizing:border-box}
html,body{width:849px;height:1200px;overflow:hidden;background:var(--white)}
.poster{position:absolute;inset:6px;border:12px solid var(--frame);background:var(--cream);overflow:hidden}
.heading{position:absolute;top:18px;left:0;right:0;text-align:center;font-family:Anton,sans-serif;font-weight:400;font-size:46px;color:var(--navy);letter-spacing:1px;line-height:1}
.sheet{position:absolute;top:82px;left:34px;width:745px;font-family:Oswald,sans-serif;font-weight:700;text-transform:uppercase;line-height:1}
.row{display:flex;align-items:center;gap:10px;white-space:nowrap;margin-bottom:6px}
.row.spread{justify-content:space-between}
.big{font-family:Anton,sans-serif;font-weight:400;font-size:44px;letter-spacing:.5px;line-height:1.02}
.huge{font-family:Anton,sans-serif;font-weight:400;font-size:70px;line-height:1}
.mid{font-size:25px;line-height:1.1}
.small{font-size:15px;line-height:1.1}
.stack{display:flex;flex-direction:column}
.navy{color:var(--navy)}.teal{color:var(--teal)}.orange{color:var(--orange)}
.group{display:flex;align-items:center;gap:8px}
.wide{font-size:50px}
.closing{display:flex;justify-content:space-between;margin-left:200px;gap:14px;white-space:nowrap}
.closing .stack{gap:4px}
.brand{position:absolute;left:34px;bottom:30px;display:flex;align-items:center;gap:8px;font-family:Oswald,sans-serif;font-weight:700;font-size:28px;color:var(--teal);line-height:1}
.brand-dot{width:20px;height:20px;border-radius:50%;background:var(--orange)}
</style>
</head>
<body>
<main class="poster">
  <h1 class="heading">Nurses' Manifesto</h1>
  <section class="sheet">
    <div class="row spread">
      <div class="stack">
        <span class="huge teal">Nurse</span>
        <span class="small navy">With open hands,<br>hearts &amp; minds.</span>
      </div>
      <div class="stack">
        <span class="mid navy">Look after</span>
        <span class="group"><span class="big orange">Yourself</span><span class="mid navy">&amp; value</span></span>
        <span class="small navy">Your health as much as you<br>value the health of others.</span>
      </div>
    </div>
    <div class="row">
      <span class="small orange">Delight your clients &amp;<br>colleagues by exceeding their</span>
      <span class="big navy wide">Expectations</span>
    </div>
    <div class="row"><span class="big navy wide">Deliver care skillfully.</span></div>
    <div class="row spread">
      <div class="stack">
        <span class="group"><span class="big teal">Respect</span><span class="small navy">the limits of</span></span>
        <span class="small navy">People's knowledge &amp; share your<br>knowledge generously.</span>
      </div>
      <div class="stack">
        <span class="group"><span class="big orange">Support</span><span class="small navy">your colleagues</span></span>
        <span class="group"><span class="small navy">&amp; champion their</span><span class="big orange">Purpose.</span></span>
      </div>
    </div>
    <div class="row"><span class="big navy">Learn something new each day.</span></div>
    <div class="row"><span class="small orange">Trust your knowledge &amp; seek advice only from respected sources.</span></div>
    <div class="row"><span class="big orange">Be a lifelong learner.</span></div>
    <div class="row"><span class="big navy">Celebrate, respect &amp; value</span></div>
    <div class="row"><span class="mid teal">The diversity of Australian culture.</span></div>
    <div class="row spread">
      <div class="stack">
        <span class="group"><span class="big orange">Smile</span><span class="small navy">&amp; infect others<br>with your</span></span>
        <span class="mid teal">Happiness &amp; have fun!</span>
      </div>
      <div class="stack">
        <span class="group"><span class="small navy">Always do the</span><span class="big navy">Right</span></span>
        <span class="group"><span class="big navy">Thing</span><span class="small navy">without exception.</span></span>
      </div>
    </div>
    <div class="row spread">
      <span class="group"><span class="small teal">You are unique,<br>revel in your</span><span class="big navy">Individuality.</span></span>
      <span class="group"><span class="small orange">Always be<br>focused.</span><span class="big navy">Solution</span></span>
    </div>
    <div class="row"><span class="big navy">Seek success firstly from within.</span></div>
    <div class="row spread">
      <span class="small"><span class="orange">Only follow exceptional leaders.</span><br><span class="navy">If there is no one left to follow, then lead!</span></span>
      <span class="small navy">Always lead with<br>purpose, passion<br>&amp; commitment.</span>
    </div>
    <div class="row">
      <span class="small navy">Respond to complex situations innovatively,<br>creatively &amp; safely within the scope of</span>
      <span class="big orange">Your practice.</span>
    </div>
    <div class="closing">
      <div class="stack">
        <span class="group"><span class="small navy">Adopt a</span><span class="big orange">'Can do'</span></span>
        <span class="small navy">Attitude to everything<br>that comes your way.</span>
      </div>
      <div class="stack">
        <span class="mid navy">Choose your thoughts wisely,</span>
        <span class="mid navy">They create your reality.</span>
        <span class="big teal">Live your dream.</span>
      </div>
    </div>
  </section>
  <div class="brand"><span class="brand-dot"></span>CalmPeak</div>
</main>
</body>
</html>
```